Thornbury Building Company - Card Design

I am looking to use the logo designs that you already did for me to develop a business card. I would like the card to have a black background and be double sided. I want white and green logo and text. I have attached an inspiration photo of a look that I like. I would like to use the Vertical Logo attached to take up the full front side of the card. On the back where I have my name and information, I would like to have the horizontal logo or maybe even just the image of the 'A' and trees without the text. I am open, but I am looking for something clean and simple and I want the green to really pop! Additional files can be found under Design #: 58302946

Target Market(s)

Homeowners

Industry/Entity Type

Construction

Contact Information for Business Card

Name: Marcus Thornbury, Title: Project Manager, Phone: 555.274.8136, Email: thornburybuildingcompany@mailvesta.com, address: 487 Larkspur Ln, Felton, CA 95033, Lic# 2468317

Colors
00AB8E
00BBA5
67D7C9
C6EFE9
E9F9F6

Requirements
Nice to have
• I would like to see the logos that I have already got from ArtLoomHub, though I am open to new ones

```html
<!DOCTYPE html>
<html lang="en">
<head>
<meta charset="utf-8">
<title>Thornbury Building Company – Business Card</title>
<link rel="stylesheet" href="https://fonts.googleapis.com/css2?family=Montserrat:wght@600;700;800&display=swap">
<style>
  :root {
    --page-bg: #e9e6e1;
    --card-bg: #121212;
    --brand-green: #6ab547;
    --brand-green-deep: #58a23a;
    --brand-white: #ffffff;
    --card-radius: 34px;
  }
  * { box-sizing: border-box; margin: 0; padding: 0; }
  html, body {
    width: 1200px; height: 1200px; overflow: hidden;
    background: var(--page-bg);
    font-family: "Montserrat", Arial, sans-serif;
  }
  .sheet {
    width: 1200px; height: 1200px;
    display: flex; flex-direction: column;
    align-items: center; justify-content: center; gap: 60px;
  }
  .card {
    position: relative;
    width: 875px; height: 500px;
    background: var(--card-bg);
    border-radius: var(--card-radius);
    overflow: hidden;
    box-shadow: 0 6px 18px rgba(0,0,0,.18);
  }
  .wordmark {
    font-weight: 800;
    color: var(--brand-white);
    text-transform: uppercase;
    letter-spacing: 2px;
    line-height: 1.05;
  }

  /* Front */
  .card--front {
    display: flex; flex-direction: column;
    align-items: center; justify-content: center;
  }
  .logo-mark-area {
    width: 230px; height: 140px;
    background: linear-gradient(180deg, var(--brand-green), var(--brand-green-deep));
    margin-bottom: 22px;
  }
  .card--front .wordmark { font-size: 54px; text-align: center; }
  .social-row {
    margin-top: 40px;
    display: flex; align-items: center; gap: 22px;
    color: var(--brand-green);
    font-weight: 700; font-size: 20px; text-transform: uppercase;
  }
  .social-item { display: flex; align-items: center; gap: 8px; font-size: 16px; text-transform: none; }
  .social-dot {
    width: 18px; height: 18px; border-radius: 50%;
    background: var(--brand-green);
  }

  /* Back */
  .card--back { padding: 44px 60px; }
  .card--back .wordmark { font-size: 48px; }
  .contact {
    position: absolute; left: 60px; top: 178px;
    color: var(--brand-green);
  }
  .contact__name { color: var(--brand-white); font-size: 26px; font-weight: 800; }
  .contact__title { font-size: 16px; font-weight: 700; text-transform: uppercase; letter-spacing: 2px; margin-top: 2px; }
  .contact__phone { font-size: 46px; font-weight: 800; letter-spacing: 1px; margin-top: 14px; line-height: 1.1; }
  .contact__line { font-size: 17px; font-weight: 700; margin-top: 6px; }
  .back-mark-area {
    position: absolute; right: 0; bottom: 0;
    width: 340px; height: 290px;
    background: linear-gradient(160deg, var(--brand-green), var(--brand-green-deep));
  }
</style>
</head>
<body>
<main class="sheet">
  <section class="card card--front" aria-label="Card front">
    <div class="logo-mark-area" role="img" aria-label="Company logo symbol: house with pine trees"></div>
    <h1 class="wordmark">Thornbury<br>Building Company</h1>
    <div class="social-row">
      <span>Find us on:</span>
      <span class="social-item"><span class="social-dot"></span>Friendsphere</span>
      <span class="social-item"><span class="social-dot"></span>Pictoria</span>
      <span class="social-item"><span class="social-dot"></span>Chirpline</span>
    </div>
  </section>

  <section class="card card--back" aria-label="Card back">
    <h2 class="wordmark">Thornbury<br>Building Company</h2>
    <div class="contact">
      <p class="contact__name">Marcus Thornbury</p>
      <p class="contact__title">Project Manager</p>
      <p class="contact__phone">555.274.8136</p>
      <p class="contact__line">thornburybuildingcompany@mailvesta.com</p>
      <p class="contact__line">www.thornburybuild.com</p>
      <p class="contact__line">487 Larkspur Ln, Felton, CA 95033</p>
      <p class="contact__line">Lic# 2468317</p>
    </div>
    <div class="back-mark-area" role="img" aria-label="Large company logo symbol: house with pine trees"></div>
  </section>
</main>
</body>
</html>
```